Wendmoor Vapes labels

We need a label designed for our e-liquid that we will be selling from our store. (E-liquid is used in electronic cigarettes) The label should be 1-1.5 inches tall and ~3 inches long.

Try to focus on highlighting the name brand over the specific flavor.

Bottle size will be 15ml clear bottles.

There will be 10+ flavors and each flavor will need a slightly different label (with the same overall theme) and different nicotine levels varying from 0mg, 6mg, 12mg, and 18mg.

Initial favor list is:
Copper Lagoon
Velvet Slurp
Zesty Figs
Tumble Plums
Guava Riot
Fizzy Gems
Amber Falcon
Frostleaf
Glowstone
Marlo
Maple Twirl

Please add the following warning in caps and small font:

(WHITE FONT)
This product contains nicotine or was produced at a facility that processes nicotine which has been known to cause birth defects and other reproductive harm. This product also contains VG/PG and artificial flavors. Not for sale to minors.
(RED FONT)
Toxic if swallowed or has contact with skin. Keep locked up and out of reach of children and pets. In case of accident or you feel unwell seek medical advice immediately.

Target Market(s)

young adults

Industry/Entity Type

Electronic

```html
<!DOCTYPE html>
<html lang="en">
<head>
<meta charset="utf-8">
<title>Wendmoor Vapes – Velvet Slurp Labels</title>
<link href="https://fonts.googleapis.com/css2?family=Oswald:wght@300;400&display=swap" rel="stylesheet">
<style>
  :root {
    --page: #ffffff;
    --label-black: #060608;
    --purple: #8a3c98;
    --purple-dark: #5d2b80;
    --purple-mid: #7a3a9e;
    --brand-blue: #2f7fd0;
    --warning-purple: #8e4fa6;
    --white: #ffffff;
    --glass-light: #f2f4f5;
    --glass-mid: #dfe3e6;
  }
  * { margin: 0; padding: 0; box-sizing: border-box; }
  html, body { width: 1200px; height: 1000px; overflow: hidden; background: var(--page); }
  body { position: relative; font-family: "Oswald", sans-serif; }

  .label {
    position: absolute;
    left: 118px;
    width: 678px;
    height: 340px;
    background: var(--label-black);
    overflow: hidden;
  }
  .label--first { top: 100px; }
  .label--second { top: 558px; }

  .warning-column {
    position: absolute;
    top: 10px;
    height: 320px;
    writing-mode: vertical-rl;
    transform: rotate(180deg);
    font-weight: 300;
    font-size: 10.2px;
    line-height: 18px;
    letter-spacing: 0.05px;
  }
  .warning-column--left { left: 18px; width: 60px; color: var(--warning-purple); }
  .warning-column--right { left: 572px; width: 60px; color: var(--white); }

  .nicotine-band {
    position: absolute;
    left: 82px;
    top: 0;
    width: 42px;
    height: 340px;
    background: var(--purple);
  }
  .nicotine-band span {
    position: absolute;
    left: 0;
    bottom: 74px;
    width: 42px;
    writing-mode: vertical-rl;
    transform: rotate(180deg);
    color: var(--white);
    font-size: 18px;
    font-weight: 400;
    line-height: 42px;
    white-space: nowrap;
  }

  .seam-strip {
    position: absolute;
    left: 550px;
    top: 0;
    width: 12px;
    height: 340px;
    background: var(--purple-dark);
  }

  .brand-name {
    position: absolute;
    left: 124px;
    width: 426px;
    top: 36px;
    text-align: center;
    color: var(--brand-blue);
    font-size: 32px;
    font-weight: 400;
    letter-spacing: 2px;
    text-transform: uppercase;
  }
  .brand-mark {
    position: absolute;
    left: 297px;
    top: 128px;
    width: 80px;
    height: 80px;
    border-radius: 50%;
    background: var(--brand-blue);
  }
  .label--second .brand-mark { background: var(--purple-mid); }

  .flavor-ribbon {
    position: absolute;
    left: 212px;
    top: 266px;
    width: 230px;
    height: 60px;
  }
  .flavor-ribbon svg { position: absolute; inset: 0; }
  .flavor-ribbon span {
    position: absolute;
    left: 0;
    right: 0;
    top: 14px;
    text-align: center;
    color: var(--white);
    font-size: 20px;
    font-weight: 300;
    text-transform: uppercase;
  }

  .bottle-mockup {
    position: absolute;
    left: 885px;
    width: 150px;
    height: 425px;
    border-radius: 40px 40px 22px 22px;
    background: linear-gradient(90deg, var(--glass-mid), var(--glass-light) 40%, var(--glass-mid));
  }
  .bottle-mockup--first { top: 45px; }
  .bottle-mockup--second { top: 505px; }
</style>
</head>
<body>

<section class="label label--first">
  <p class="warning-column warning-column--left">This product contains nicotine or was produced at a facility that processes nicotine which has been known to cause birth defects and other reproductive harm. This product also contains VG/PG and artificial flavors. Not for sale to minors.</p>
  <div class="nicotine-band"><span>Nicotine by volume: 0mg/mL</span></div>
  <h1 class="brand-name">Wendmoor Vapes</h1>
  <div class="brand-mark"></div>
  <div class="flavor-ribbon">
    <svg viewBox="0 0 230 60" width="230" height="60">
      <polygon points="0,12 40,12 40,52 0,52 12,32" fill="#5d2b80"/>
      <polygon points="230,12 190,12 190,52 230,52 218,32" fill="#5d2b80"/>
      <polygon points="22,4 208,4 208,48 22,48" fill="#8a3c98"/>
      <polygon points="115,4 208,4 208,48 115,48" fill="#6e3591"/>
    </svg>
    <span>Velvet Slurp</span>
  </div>
  <div class="seam-strip"></div>
  <p class="warning-column warning-column--right">This product contains nicotine or was produced at a facility that processes nicotine which has been known to cause birth defects and other reproductive harm. This product also contains VG/PG and artificial flavors. Not for sale to minors.</p>
</section>

<section class="label label--second">
  <p class="warning-column warning-column--left">This product contains nicotine or was produced at a facility that processes nicotine which has been known to cause birth defects and other reproductive harm. This product also contains VG/PG and artificial flavors. Not for sale to minors.</p>
  <div class="nicotine-band"><span>Nicotine by volume: 0mg/mL</span></div>
  <h2 class="brand-name">Wendmoor Vapes</h2>
  <div class="brand-mark"></div>
  <div class="flavor-ribbon">
    <svg viewBox="0 0 230 60" width="230" height="60">
      <polygon points="0,12 40,12 40,52 0,52 12,32" fill="#5d2b80"/>
      <polygon points="230,12 190,12 190,52 230,52 218,32" fill="#5d2b80"/>
      <polygon points="22,4 208,4 208,48 22,48" fill="#8a3c98"/>
      <polygon points="115,4 208,4 208,48 115,48" fill="#6e3591"/>
    </svg>
    <span>Velvet Slurp</span>
  </div>
  <div class="seam-strip"></div>
  <p class="warning-column warning-column--right">This product contains nicotine or was produced at a facility that processes nicotine which has been known to cause birth defects and other reproductive harm. This product also contains VG/PG and artificial flavors. Not for sale to minors.</p>
</section>

<div class="bottle-mockup bottle-mockup--first" role="img" aria-label="Clear dropper bottle wearing the blue-accent Velvet Slurp label"></div>
<div class="bottle-mockup bottle-mockup--second" role="img" aria-label="Clear dropper bottle wearing the purple-accent Velvet Slurp label"></div>

</body>
</html>
```